Customer Facing Document Design

Looking for professional design in Word for 5 Templates:

- Purchase Contract
- Sales Contract
- Packing List
- Settlement Report
- Invoice

I have attached our current designs and also some example designs that we want to look similar to. We want our company logo included on all documents. On the Purchase Order, Sales Order, Settlement Report, Invoice we also want our ISO accreditation picture and KRBA logo included.

```html
<!DOCTYPE html>
<html lang="en">
<head>
<meta charset="utf-8">
<title>Sales Order</title>
<link href="https://fonts.googleapis.com/css2?family=Arimo:wght@400;700&family=Tinos:wght@700&display=swap" rel="stylesheet">
<style>
:root{
  --ink:#000;
  --title-blue:#2e3192;
  --head-navy:#1f1f6b;
  --total-red:#e8141b;
  --logo-grey:#8a8a8a;
  --badge-dark:#1a1a1a;
  --badge-grey:#6d6e71;
  --sig-tone:#f1f1f1;
  --paper:#fff;
}
*{margin:0;padding:0;box-sizing:border-box}
html,body{width:877px;height:1200px;overflow:hidden;background:var(--paper)}
body{font-family:"Arimo",Arial,sans-serif;color:var(--ink)}
.sheet{position:relative;width:877px;height:1200px}
.abs{position:absolute}
.company-contact{left:83px;top:60px;font-family:"Tinos","Times New Roman",serif;font-weight:700;font-size:13.5px;line-height:18px;text-transform:uppercase}
.brand{left:560px;top:58px;width:255px;height:86px;display:flex;align-items:center;gap:12px}
.brand-dot{width:60px;height:60px;border-radius:50%;background:var(--logo-grey);flex:none}
.brand-name{font-family:"Arimo",Arial,sans-serif;font-weight:700;font-size:38px;color:var(--logo-grey);line-height:1}
.doc-title{left:0;width:896px;top:200px;text-align:center;font-size:28px;font-weight:700;color:var(--title-blue)}
.party{top:278px;font-size:12px;font-weight:700;line-height:26px;text-transform:uppercase}
.party-label{font-size:16px;text-transform:none;line-height:24px;margin-bottom:2px}
.buyer{left:93px}
.vendor{left:311px}
.vendor .addr-line{line-height:19px;margin-top:4px}
.order-meta{left:532px;top:276px;font-size:16px;line-height:18px}
.order-meta dl{display:grid;grid-template-columns:159px auto}
.order-meta dt{font-weight:700}
.order-meta dd{font-size:15.5px}
.order-meta dd.small{font-size:14px}
.lines{left:88px;top:468px;width:740px;border-collapse:collapse;font-size:12px}
.lines th{color:var(--head-navy);font-weight:700;font-size:13px;padding-bottom:12px}
.lines td{font-weight:700;font-size:11.5px}
.lines .c-alloy{text-align:left;width:220px}
.lines .c-desc{text-align:left;width:200px}
.lines .c-lbs{text-align:center;width:80px}
.lines .c-rate{text-align:center;width:100px}
.lines .c-total{text-align:right;width:90px}
.subtotal-label{left:453px;top:545px;font-size:17px;font-weight:700}
.subtotal-value{right:61px;top:546px;font-size:17px;font-weight:700;color:var(--total-red)}
.sign-label{top:648px;font-size:17px;font-weight:700}
.sign-vendor{left:177px}
.sign-seller{left:632px}
.signature-area{left:634px;top:681px;width:156px;height:74px;background:var(--sig-tone)}
.badge-iso{left:114px;top:938px;width:164px;height:223px}
.badge-accred{left:285px;top:948px;width:215px;height:210px}
.partner{left:540px;top:1030px;display:flex;align-items:center;gap:12px}
.partner-name{font-size:44px;font-weight:700;color:var(--badge-grey);line-height:1}
.partner-dot{width:44px;height:44px;border-radius:50%;background:var(--badge-grey)}
</style>
</head>
<body>
<main class="sheet">
  <address class="abs company-contact" style="font-style:normal">
    Norvane Alloys &amp; Metals,<br>
    LLC sales@norvane-am.com<br>
    +44 7000 481920<br>
    www.norvane-am.com<br>
    4410 Linden Court, Fairmont, CA 90000
  </address>

  <div class="abs brand">
    <span class="brand-dot"></span>
    <span class="brand-name">NORVANE</span>
  </div>

  <h1 class="abs doc-title">Sales Order</h1>

  <section class="abs party buyer">
    <div class="party-label">Buyer:</div>
    <div>Ridgeway Metals, LLC</div>
    <div>780 County Road 9</div>
    <div>Marlow</div>
    <div>IL 60000</div>
  </section>

  <section class="abs party vendor">
    <div class="party-label">Vendor:</div>
    <div>Norvane A&amp;M</div>
    <div>4410 Linden Court</div>
    <div class="addr-line">Fairmont<br>CA 90000</div>
  </section>

  <section class="abs order-meta">
    <dl>
      <dt style="font-size:14px">S.O. Number:</dt><dd class="small">Ridgeway 092325</dd>
      <dt>S.O. Issue Date:</dt><dd>09/23/2025</dd>
      <dt>Deliver by:</dt><dd>September 2025</dd>
      <dt>Payment Terms:</dt><dd>Net 30</dd>
      <dt>F.O.B:</dt><dd>DDP Marlow</dd>
      <dt>Buyer’s PO:</dt><dd>8554</dd>
    </dl>
  </section>

  <table class="abs lines">
    <thead>
      <tr>
        <th class="c-alloy">Alloy</th>
        <th class="c-desc">Description</th>
        <th class="c-lbs">Lbs</th>
        <th class="c-rate">US$/Lb</th>
        <th class="c-total">Total</th>
      </tr>
    </thead>
    <tbody>
      <tr>
        <td class="c-alloy">NX2 VQ Solids</td>
        <td class="c-desc"></td>
        <td class="c-lbs">1,000</td>
        <td class="c-rate">$8.75</td>
        <td class="c-total">$8,750.00</td>
      </tr>
    </tbody>
  </table>

  <div class="abs subtotal-label">Subtotal, USD</div>
  <div class="abs subtotal-value">$8,750.00</div>

  <div class="abs sign-label sign-vendor">Vendor signature:</div>
  <div class="abs sign-label sign-seller">Norvane&nbsp; signature:</div>
  <div class="abs signature-area" role="img" aria-label="Handwritten signature of the seller"></div>

  <svg class="abs badge-iso" viewBox="0 0 164 223" role="img" aria-label="Quality certification badge">
    <circle cx="82" cy="82" r="78" fill="var(--badge-dark)"/>
    <rect x="10" y="175" width="144" height="40" fill="var(--badge-dark)"/>
  </svg>

  <svg class="abs badge-accred" viewBox="0 0 215 210" role="img" aria-label="Accreditation body badge">
    <rect x="10" y="0" width="195" height="210" fill="var(--badge-dark)"/>
  </svg>

  <div class="abs partner">
    <span class="partner-name">KRBA</span>
    <span class="partner-dot"></span>
  </div>
</main>
</body>
</html>
```